Business cards for Norwegian software consultancy business

We are in need of business cards for our Norwegian consultancy company.
“Valto Brindex AS” specializes in software development, architecture and agile methodology, providing mostly on-site services at customers.
The cards should reflect a certain level of business professionalism with an elegant touch, while paying tribute to our modern and technological heritage. Our logo should be featured, as well as room for basic information about the cardholder and legal information of the company (company name, address and VAT number).
We would like our cards to reflect that we are a modern consulting company. It should present a professional image that people will remember. The texture and color pallette should reflect our professionalism and reliability, so we prefer a light color pallette with colors such as gray, white, blue and black. The number of colors used should however not be overwhelming, with the text being distinct and readable.
We are open to untraditional layouts and playful designs as long as they communicate the intent stated above.
You could also take a look at our website http://www.brindex.no for input on our visual profile.
Our logo is attached in the form of vectors and rasterized PNG. Please comment if you would like the black-white and/or inverted versions as well.
Industry/Entity Type
Architecture
Contact Information for Business Card
Company information:
Valto Brindex AS
Kvernlia 14, 3170 Sem
482 71 519
info@brindex.no
www.brindex.no
Employee information:
Full name
Title
Email
Phone
Font styles to use
Look and feel

```html
<!DOCTYPE html>
<html lang="no">
<head>
<meta charset="utf-8">
<title>Valto Brindex AS – Business Cards</title>
<link href="https://fonts.googleapis.com/css2?family=Open+Sans:wght@400;600;700&display=swap" rel="stylesheet">
<style>
  :root {
    --ink: #111111;
    --text: #1a1a1a;
    --blue: #4a9bd6;
    --card: #ffffff;
    --stage: #e9e6e1;
  }
  * { margin: 0; padding: 0; box-sizing: border-box; }
  html, body {
    width: 1200px; height: 749px; overflow: hidden;
    background: var(--stage);
    font-family: "Open Sans", Arial, sans-serif;
    color: var(--text);
  }
  .canvas { position: relative; width: 1200px; height: 749px; }
  .card {
    position: absolute; top: 200px; height: 310px;
    background: var(--card); overflow: hidden;
  }
  .card--front { left: 39px; width: 547px; }
  .card--back { left: 621px; width: 544px; }

  .brand {
    position: absolute; display: flex; align-items: center;
    font-weight: 600; color: var(--ink); letter-spacing: 0.02em;
    white-space: nowrap;
  }
  .brand__square { background: var(--blue); flex: none; }
  .card--front .brand {
    left: 0; right: 0; top: 128px; justify-content: center;
    font-size: 40px; gap: 14px;
  }
  .card--front .brand__square { width: 30px; height: 30px; }
  .card--back .brand {
    left: 22px; top: 42px; font-size: 34px; gap: 12px;
  }
  .card--back .brand__square { width: 26px; height: 26px; }

  .holder { position: absolute; left: 132px; top: 138px; font-size: 12.5px; line-height: 15.5px; }
  .holder__name { font-weight: 700; font-size: 14px; line-height: 17px; }
  .holder__company { margin-top: 21px; }
  .holder__contact { margin-top: 5px; }

  .card__band { position: absolute; left: 0; bottom: 0; width: 544px; height: 22px; }
</style>
</head>
<body>
<main class="canvas">
  <section class="card card--front" aria-label="Card front">
    <div class="brand"><span class="brand__square"></span>Valto Brindex</div>
  </section>

  <section class="card card--back" aria-label="Card back">
    <div class="brand"><span class="brand__square"></span>Valto Brindex</div>
    <div class="holder">
      <p class="holder__name">Henrik Solvang</p>
      <p class="holder__title">Manger</p>
      <p class="holder__company">Valto Brindex AS Kvernlia<br>14, 3170 Sem 482 71 519</p>
      <p class="holder__contact">t: + 999 999 9999<br>e: info@brindex.no<br>www.brindex.no</p>
    </div>
    <svg class="card__band" viewBox="0 0 544 22" aria-hidden="true">
      <polygon points="0,0 312,0 320,22 0,22" fill="var(--ink)"/>
      <polygon points="320,8 544,8 544,22 326,22" fill="var(--blue)"/>
    </svg>
  </section>
</main>
</body>
</html>
```